Design for schnapps bottle label "Río Ámbar"

Hi! On a small land lot we are producing our own Italian schnapps "Grappa". For the bottles we would like to modernize our current labes that you find below. The two cats looking at each other should remain, but updated and more modern. I am very much looking forward to your suggestions. Best, Jens

Target Market(s)

Schnapps bottle label

Requirements
Must have
• Cats should resemble the cats that are decorating the house entry (see attached), however, should have a more modern appearance.

Text elements should remain: "Grappa", "Río Ámbar", "Legnoso", "[Vintage Year], "Raccolta No", "Vol %"
Should not have
• Current ornament can be used, replaced or deleted (whatever looks best)

```html
<!DOCTYPE html>
<html lang="it">
<head>
<meta charset="utf-8">
<title>Grappa legnoso 2015 – Río Ámbar label</title>
<link rel="stylesheet" href="https://fonts.googleapis.com/css2?family=Berkshire+Swash&family=Allura&family=Cinzel:wght@400;600&display=swap">
<style>
  :root {
    --backdrop: #8b8481;
    --paper: #ededeb;
    --paper-shade: #e2e2e0;
    --ink: #1f1e1e;
    --olive: #8f961c;
    --olive-light: #b4b83a;
    --olive-dark: #6c7013;
  }
  * { margin: 0; padding: 0; box-sizing: border-box; }
  html, body {
    width: 1200px;
    height: 800px;
    overflow: hidden;
    background: var(--backdrop);
  }
  .canvas {
    position: relative;
    width: 1200px;
    height: 800px;
  }
  .label {
    position: absolute;
    left: 364px;
    top: 40px;
    width: 472px;
    height: 720px;
    background: radial-gradient(ellipse at 50% 40%, var(--paper) 0%, var(--paper-shade) 100%);
    overflow: hidden;
    box-shadow: 0 6px 24px rgba(0, 0, 0, 0.25);
  }
  .top-band {
    position: absolute;
    left: 0; top: 0;
    width: 100%;
    height: 35px;
    background: linear-gradient(
      to bottom,
      var(--olive-dark) 0 9px,
      var(--olive) 9px 20px,
      var(--olive-dark) 20px 24px,
      var(--olive-light) 24px 35px
    );
  }
  .product-name {
    position: absolute;
    left: 0; top: 66px;
    width: 100%;
    text-align: center;
    font-family: "Berkshire Swash", serif;
    font-size: 88px;
    font-weight: 400;
    line-height: 1;
    color: var(--ink);
    text-shadow: 2px 2px 0 rgba(0, 0, 0, 0.15);
  }
  .style-line {
    position: absolute;
    left: 0; top: 206px;
    width: 100%;
    height: 60px;
    text-align: center;
    white-space: nowrap;
    line-height: 60px;
  }
  .style-name {
    font-family: "Allura", cursive;
    font-size: 50px;
    color: var(--ink);
  }
  .vintage {
    font-family: "Cinzel", serif;
    font-weight: 600;
    font-size: 26px;
    color: var(--olive);
    margin-left: 4px;
  }
  .connector {
    position: absolute;
    left: 0; top: 268px;
    width: 100%;
    text-align: center;
    font-family: "Allura", cursive;
    font-size: 38px;
    line-height: 40px;
    color: var(--ink);
  }
  .cats-artwork {
    position: absolute;
    left: 62px; top: 318px;
    width: 350px;
    height: 102px;
  }
  .cat-shape {
    position: absolute;
    top: 0;
    width: 164px;
    height: 102px;
    background: linear-gradient(to bottom, #3a3939, var(--ink));
  }
  .cat-shape.left { left: 0; border-radius: 50px 40px 6px 6px; }
  .cat-shape.right { right: 0; border-radius: 40px 50px 6px 6px; }
  .brand-name {
    position: absolute;
    left: 0; top: 440px;
    width: 100%;
    text-align: center;
    font-family: "Berkshire Swash", serif;
    font-size: 60px;
    font-weight: 400;
    line-height: 1.3;
    color: var(--olive-dark);
    white-space: nowrap;
  }
  .lot-number, .strength {
    position: absolute;
    top: 562px;
    line-height: 30px;
    color: var(--ink);
    white-space: nowrap;
  }
  .lot-number { left: 20px; }
  .strength { right: 20px; }
  .script { font-family: "Allura", cursive; font-size: 24px; }
  .serif { font-family: "Cinzel", serif; font-size: 16px; }
  .bottom-band {
    position: absolute;
    left: 0; bottom: 0;
    width: 100%;
    height: 119px;
    border-top: 4px solid var(--olive);
    background: linear-gradient(to bottom, var(--olive) 0%, var(--olive-dark) 100%);
  }
</style>
</head>
<body>
  <main class="canvas">
    <section class="label" aria-label="Grappa bottle label">
      <div class="top-band"></div>
      <h1 class="product-name">Grappa</h1>
      <p class="style-line">
        <span class="style-name">“legnoso”</span><span class="vintage">2015</span>
      </p>
      <p class="connector">di</p>
      <div class="cats-artwork" role="img" aria-label="Two black cat silhouettes crouching and facing each other">
        <div class="cat-shape left"></div>
        <div class="cat-shape right"></div>
      </div>
      <h2 class="brand-name">Río Ámbar</h2>
      <p class="lot-number"><span class="script">Raccolta No.</span> <span class="serif">01</span></p>
      <p class="strength"><span class="serif">41.0</span> <span class="script">Vol</span></p>
      <div class="bottom-band" role="img" aria-label="Olive band with monogram and ornamental pattern"></div>
    </section>
  </main>
</body>
</html>
```